We need a card and logo design for a new business based in Dallas Texas called Stonemarsh Financial LLC.

We provide bridge loans.We offer pay day loans,title loans and check cashing.Our products are emmergency loans that help borrowers meet short term liquidity needs until the next pay check.

The final design should communicate,professionalism,Sophistication and friendliness to our customers.Use the color Blue as much as possible and another eye catching color if possible.We will consider a profesional looking knight logo with the color Blue in it.Please design a full corporate identity.

```html
<!DOCTYPE html>
<html lang="en">
<head>
<meta charset="utf-8">
<title>Stonemarsh Financial LLC – Business Card</title>
<link rel="stylesheet" href="https://fonts.googleapis.com/css2?family=Cinzel:wght@500;600&family=Open+Sans:wght@400;600;700&display=swap">
<style>
  :root {
    --bg: #2e2a28;
    --card-light: #f1f2f4;
    --navy: #2a3a7c;
    --label-blue: #2f4a8a;
    --ink: #1a1a1a;
    --rule: #8a8a8a;
    --blue-core: #0b57ab;
    --blue-edge: #1e3e80;
    --white: #ffffff;
  }
  * { margin: 0; padding: 0; box-sizing: border-box; }
  html, body { width: 1000px; height: 1200px; overflow: hidden; }
  body { background: var(--bg); position: relative; font-family: "Open Sans", Arial, sans-serif; }

  .card { position: absolute; width: 723px; height: 423px; overflow: hidden; }
  .card--front { left: 140px; top: 119px; background: var(--card-light); }
  .card--back {
    left: 125px; top: 638px;
    background: radial-gradient(ellipse at 50% 45%, var(--blue-core) 0%, #0d4fa0 35%, var(--blue-edge) 100%);
  }

  .holder { position: absolute; right: 36px; top: 44px; text-align: right; }
  .holder__name { font-family: "Cinzel", Georgia, serif; font-weight: 600; font-size: 27px; color: var(--navy); letter-spacing: 0.5px; line-height: 1.1; }
  .holder__title { font-weight: 600; font-size: 17px; color: var(--ink); margin-top: 4px; }

  .brand { position: absolute; left: 0; width: 100%; text-align: center; font-family: "Cinzel", Georgia, serif; font-weight: 600; }
  .brand__name { display: block; letter-spacing: 1px; line-height: 1.1; }
  .brand__legal { display: block; letter-spacing: 1px; line-height: 1.1; }
  .brand--front { top: 176px; color: var(--navy); }
  .brand--front .brand__name { font-size: 40px; }
  .brand--front .brand__legal { font-size: 25px; margin-top: 4px; }
  .brand--back { top: 268px; color: var(--white); }
  .brand--back .brand__name { font-size: 46px; }
  .brand--back .brand__legal { font-size: 28px; margin-top: 4px; }

  .watermark { position: absolute; right: -10px; top: 230px; }

  .contact { position: absolute; top: 305px; font-size: 16px; color: var(--ink); }
  .contact--left { left: 51px; }
  .contact--right { left: 393px; }
  .contact__row { display: flex; line-height: 22px; margin-bottom: 9px; }
  .contact__label { color: var(--label-blue); font-weight: 700; font-size: 15px; }
  .contact--left .contact__label { width: 62px; }
  .contact--right .contact__label { width: 75px; }
  .contact__divider { position: absolute; left: 374px; top: 298px; width: 1px; height: 80px; background: var(--rule); }
</style>
</head>
<body>

  <section class="card card--front" aria-label="Card front">
    <svg class="watermark" width="200" height="200" viewBox="0 0 200 200" aria-hidden="true">
      <circle cx="100" cy="100" r="95" fill="#ffffff" opacity="0.7"/>
    </svg>

    <div class="holder">
      <div class="holder__name">DANIEL REYES</div>
      <div class="holder__title">Financial Advisor</div>
    </div>

    <div class="brand brand--front">
      <span class="brand__name">STONEMARSH</span>
      <span class="brand__legal">FINANCIAL LLC.</span>
    </div>

    <div class="contact contact--left">
      <div class="contact__row"><span class="contact__label">Phone:</span><span>111-123-4567</span></div>
      <div class="contact__row"><span class="contact__label">Email:</span><span>info@stonemarshfinancial.com</span></div>
    </div>
    <div class="contact__divider"></div>
    <div class="contact contact--right">
      <div class="contact__row"><span class="contact__label">Fax:</span><span>111-123-4567</span></div>
      <div class="contact__row"><span class="contact__label">Address:</span><span>XXX Some Street Address<br>State, Country</span></div>
    </div>
  </section>

  <section class="card card--back" aria-label="Card back">
    <div class="brand brand--back">
      <span class="brand__name">STONEMARSH</span>
      <span class="brand__legal">FINANCIAL LLC.</span>
    </div>
  </section>

</body>
</html>
```